Business Card and Letterhead for Pimlu - modern real estate business

I need a double sided business card design for Pimlu. Please see business card brief here https://files.trelvonadocs.com/sheet/r/7QzTmWbaXLJnoPEd-kRyUgFhHsstbvCe2qfoMxDa_pz/view?mode=shared

Please feel free to design the business cards however you feel best. I am happy to give some creative freedoms and then provide feedback from there.

Please then also create a letterhead to match the business card design

Colors

Designer to choose colors to be used in the design.

Requirements
Must have
• Must be a modern, elegant business card which looks very professional

```html
<!DOCTYPE html>
<html lang="en">
<head>
<meta charset="utf-8">
<title>Pimlu – Business Card</title>
<link rel="stylesheet" href="https://fonts.googleapis.com/css2?family=Roboto:wght@400;500;700&display=swap">
<style>
  :root {
    --brand-red: #e51c23;
    --brand-red-deep: #d4141b;
    --ink: #3a3a3a;
    --paper: #ffffff;
    --backdrop: #d8d8d5;
    --photo-light: #f4f4f4;
    --photo-dark: #33363d;
  }
  * { box-sizing: border-box; margin: 0; padding: 0; }
  html, body {
    width: 1200px; height: 801px; overflow: hidden;
    background: var(--backdrop);
    font-family: "Roboto", Arial, sans-serif;
  }
  .stage { position: relative; width: 1200px; height: 801px; }
  .card {
    position: absolute; top: 235px;
    width: 540px; height: 330px;
    box-shadow: 0 6px 18px rgba(0,0,0,0.18);
    overflow: hidden;
  }
  /* Front side */
  .card-front { left: 40px; background: var(--paper); }
  .front-wordmark {
    position: absolute; left: 30px; top: 46px;
    font-size: 40px; font-weight: 500; letter-spacing: 3px; line-height: 1;
    color: var(--brand-red); text-transform: uppercase;
  }
  .contact-block { position: absolute; left: 32px; font-size: 12.5px; color: var(--ink); line-height: 17px; white-space: nowrap; }
  .contact-office { top: 112px; }
  .contact-agent { top: 210px; }
  .contact-line { display: flex; align-items: center; gap: 6px; }
  .lic-label { color: var(--brand-red); }
  .icon { width: 11px; height: 11px; flex: none; }
  .agent-photo {
    position: absolute; right: 30px; top: 40px;
    width: 240px; height: 256px;
    background: linear-gradient(180deg, var(--photo-light) 0%, #d2d2d2 30%, var(--photo-dark) 60%, #2a2d33 100%);
  }
  .front-band {
    position: absolute; left: 0; bottom: 0;
    width: 100%; height: 34px;
    background: var(--brand-red);
    display: flex; align-items: center; justify-content: space-between;
    padding: 0 18px; color: var(--paper);
    white-space: nowrap;
  }
  .band-web { display: flex; align-items: center; gap: 8px; font-size: 15px; letter-spacing: 0.5px; }
  .band-agent { font-size: 13px; letter-spacing: 0.3px; }
  .agent-name { font-weight: 700; font-size: 15px; text-transform: uppercase; margin-right: 6px; }
  /* Back side */
  .card-back {
    left: 620px;
    background: linear-gradient(160deg, var(--brand-red) 0%, var(--brand-red-deep) 100%);
    display: flex; align-items: center; justify-content: center;
  }
  .back-wordmark {
    font-size: 96px; font-weight: 500; letter-spacing: 10px; line-height: 1;
    color: var(--paper); text-transform: uppercase;
  }
</style>
</head>
<body>
<main class="stage">
  <section class="card card-front" aria-label="Business card front">
    <div class="front-wordmark">Pimlu</div>

    <div class="contact-block contact-office">
      <div class="contact-line">PO Box 7316</div>
      <div class="contact-line">Calderwood NSW 2690</div>
      <div class="contact-line"><span class="lic-label">Lic No.</span> 30471182</div>
      <div class="contact-line">
        <svg class="icon" viewBox="0 0 12 12"><circle cx="6" cy="6" r="6" fill="var(--brand-red)"/><path d="M3.5 4.2c.4 1.8 2 3.5 4.3 4.3l.9-.9-1.2-1-.7.5c-.8-.4-1.4-1-1.8-1.8l.5-.7-1-1.2z" fill="#fff"/></svg>
        02 4190 3357
      </div>
      <div class="contact-line">
        <svg class="icon" viewBox="0 0 12 12"><rect x="0.7" y="2.2" width="10.6" height="7.6" fill="none" stroke="var(--brand-red)" stroke-width="1"/><path d="M0.7 2.2 6 6.6l5.3-4.4M0.7 9.8l4-3.6M11.3 9.8l-4-3.6" fill="none" stroke="var(--brand-red)" stroke-width="1"/></svg>
        info@pimlu.com
      </div>
    </div>

    <div class="contact-block contact-agent">
      <div class="contact-line"><span class="lic-label">Lic No.</span> 40588216</div>
      <div class="contact-line">
        <svg class="icon" viewBox="0 0 12 12"><circle cx="6" cy="6" r="6" fill="var(--brand-red)"/><path d="M3.5 4.2c.4 1.8 2 3.5 4.3 4.3l.9-.9-1.2-1-.7.5c-.8-.4-1.4-1-1.8-1.8l.5-.7-1-1.2z" fill="#fff"/></svg>
        0412 508 194
      </div>
      <div class="contact-line">
        <svg class="icon" viewBox="0 0 12 12"><rect x="0.7" y="2.2" width="10.6" height="7.6" fill="none" stroke="var(--brand-red)" stroke-width="1"/><path d="M0.7 2.2 6 6.6l5.3-4.4M0.7 9.8l4-3.6M11.3 9.8l-4-3.6" fill="none" stroke="var(--brand-red)" stroke-width="1"/></svg>
        dean@pimlu.com
      </div>
    </div>

    <div class="agent-photo" role="img" aria-label="Portrait photo of the agent in a dark suit on a white background"></div>

    <div class="front-band">
      <div class="band-web">
        <svg class="icon" viewBox="0 0 12 12" style="width:14px;height:14px"><circle cx="6" cy="6" r="5.5" fill="#fff"/><circle cx="6" cy="6" r="3.6" fill="none" stroke="var(--brand-red)" stroke-width="0.9"/><path d="M2.4 6h7.2M6 2.4c-1.4 1.2-1.4 6 0 7.2M6 2.4c1.4 1.2 1.4 6 0 7.2" fill="none" stroke="var(--brand-red)" stroke-width="0.8"/></svg>
        www.pimlu.com
      </div>
      <div class="band-agent"><span class="agent-name">Dean Marlow</span>Licenced Real Estate Agent</div>
    </div>
  </section>

  <section class="card card-back" aria-label="Business card back">
    <div class="back-wordmark">Pimlu</div>
  </section>
</main>
</body>
</html>
```